Website for a high end London wedding DJ company

I want a website that is fairly basic but modern. It needs to look professional and smooth. I like white and black backgrounds. I am looking for something similar to this: https://www.torvalinsky.uk - at the bottom of this page it has ravenquill reviews as well. I mainly use bimmlo reviews. This would need to be included, or at least some way of showing all my 5 star reviews on the first page, to get peoples attention.
My current website is www.marrowandtide.com
My

1 page

• A way to display my reviews. Must be modern.
• Must not look cheesy and 8

```html
<!DOCTYPE html>
<html lang="en">
<head>
<meta charset="utf-8">
<title>Marrow &amp; Tide — DJ Hire Surrey</title>
<link rel="stylesheet" href="https://fonts.googleapis.com/css2?family=Merriweather:wght@400;700&family=Quicksand:wght@400;500;600&display=swap">
<style>
:root{
  --ink:#000;
  --paper:#fff;
  --accent:#9b5140;
  --text:#555;
  --line:#bdbdbd;
  --frame:#9a9a9a;
  --star:#f5a623;
}
*{box-sizing:border-box;margin:0;padding:0}
html,body{width:1200px;height:4286px;overflow:hidden;background:var(--paper)}
body{font-family:"Quicksand",sans-serif;color:var(--text)}
.page{position:relative;width:1200px;height:4286px}
.abs{position:absolute}
.serif{font-family:"Merriweather",serif}

/* hero */
.hero{left:0;top:0;width:1200px;height:857px;background:linear-gradient(160deg,#5a3a3a 0%,#4a2a58 45%,#6a3a6e 70%,#3a2430 100%)}
.hero-shade{left:0;top:0;width:1200px;height:857px;background:rgba(40,20,50,.35)}
.brand{left:0;top:48px;width:1200px;text-align:center;font-family:"Merriweather",serif;font-size:30px;color:#fff;font-weight:400}
.nav-rule{left:111px;width:976px;height:1px;background:rgba(255,255,255,.5)}
.nav{left:111px;top:146px;width:976px;display:flex;justify-content:center;gap:30px;font-family:"Merriweather",serif;font-weight:700;font-size:15px;color:#fff;letter-spacing:.3px}
.hero-title{left:0;top:392px;width:1200px;text-align:center;font-family:"Merriweather",serif;font-weight:700;font-size:56px;line-height:54px;color:#fff}
.btn{background:var(--accent);color:#fff;border-radius:24px;font-family:"Merriweather",serif;font-weight:700;display:flex;align-items:center;justify-content:center;gap:8px}
.hero-btn{left:474px;top:518px;width:250px;height:43px;font-size:15px}
.slider-arrow{width:44px;height:44px;border-radius:50%;background:rgba(255,255,255,.35);display:flex;align-items:center;justify-content:center}
.socials{display:flex;gap:10px}
.social{width:30px;height:30px;border:2px solid #fff;border-radius:50%}
.socials.dark .social{border-color:#222;width:32px;height:32px}

/* intro */
.photo{background:linear-gradient(135deg,#3a2a4a,#7a4a8a 50%,#2a1e2e)}
.frame{border:2px solid var(--line)}
.h2{font-family:"Merriweather",serif;color:#111;font-weight:400}
.body{font-size:12.5px;line-height:21.5px;color:var(--text)}
.intro-box{left:576px;top:979px;width:519px;height:341px;background:#fff;border:2px solid var(--line)}

/* band */
.band{left:0;top:1443px;width:1200px;height:383px;background:var(--ink)}
.band-text{left:150px;top:1512px;width:900px;text-align:center;color:#fff;font-family:"Merriweather",serif;font-weight:700;font-size:27px;line-height:39px}
.tile{top:1669px;width:233px;height:240px}

/* reviews */
.review-card .rule{height:2px;background:#ddd}
.stars{color:var(--star);font-size:16px;letter-spacing:2px}

/* contact */
.contact{left:136px;top:3546px;width:971px;height:562px;background:var(--ink);border:2px solid #777}
.field{background:#fff;font-size:13px;color:#666;padding:16px 26px}
.submit{left:517px;top:3950px;width:167px;height:49px;background:var(--accent);color:#fff;font-weight:700;font-size:14px;display:flex;align-items:center;justify-content:center}
</style>
</head>
<body>
<div class="page">

  <!-- hero -->
  <div class="abs hero" role="img" aria-label="Guests dancing at a wedding reception in a timber barn"></div>
  <div class="abs hero-shade"></div>
  <div class="abs brand">Marrow &amp; Tide</div>
  <div class="abs nav-rule" style="top:128px"></div>
  <nav class="abs nav"><span>HOME</span><span>DJs</span><span>REVIEWS</span><span>GALLERY</span><span>PRICES</span><span>ABOUT</span><span>EVENT PLANNER</span></nav>
  <div class="abs nav-rule" style="top:186px"></div>
  <div class="abs slider-arrow" style="left:34px;top:426px"><svg width="12" height="12" viewBox="0 0 12 12"><path d="M8 2L4 6l4 4" fill="none" stroke="#fff" stroke-width="1.5"/></svg></div>
  <div class="abs slider-arrow" style="left:1120px;top:426px"><svg width="12" height="12" viewBox="0 0 12 12"><path d="M4 2l4 4-4 4" fill="none" stroke="#fff" stroke-width="1.5"/></svg></div>
  <h1 class="abs hero-title">WELCOME TO<br>MARROW &amp; TIDE</h1>
  <div class="abs btn hero-btn">
    <svg width="13" height="13" viewBox="0 0 24 24"><path fill="#fff" d="M6.6 10.8a15 15 0 006.6 6.6l2.2-2.2c.3-.3.7-.4 1-.2 1.1.4 2.3.6 3.6.6.6 0 1 .4 1 1V20c0 .6-.4 1-1 1A17 17 0 013 4c0-.6.4-1 1-1h3.5c.6 0 1 .4 1 1 0 1.3.2 2.5.6 3.6.1.3 0 .7-.2 1z"/></svg>
    CALL US +1 888 888 8888
  </div>
  <div class="abs socials" style="left:504px;top:756px">
    <span class="social"></span><span class="social"></span><span class="social"></span><span class="social"></span><span class="social"></span>
  </div>

  <!-- intro -->
  <div class="abs frame" style="left:591px;top:962px;width:521px;height:376px"></div>
  <div class="abs intro-box"></div>
  <div class="abs photo" style="left:87px;top:960px;width:489px;height:380px" role="img" aria-label="Bride and guests dancing under purple lights"></div>
  <h2 class="abs h2" style="left:627px;top:1020px;font-size:35px">DJ HIRE SURREY</h2>
  <p class="abs body" style="left:627px;top:1082px;width:450px">Welcome to Marrow and Tide DJ hire Surrey. With 100% 5 star reviews on Bimmlo, having only started in September 2019, we are fast becoming the number 1 DJ hire company in Surrey. Whether you are looking to book for weddings, birthday parties or any occasion full of fizz and dancing, our London and Surrey wedding DJ provides a bespoke 5 star service, guaranteed to make you want to groove.</p>
  <div class="abs btn" style="left:629px;top:1232px;width:148px;height:43px;font-size:14px">LEARN MORE</div>

  <!-- band -->
  <div class="abs band"></div>
  <p class="abs band-text">With 13 years of experience in the DJing industry, we take care of the finer details to make planning your wedding day or special celebration a smooth and enjoyable experience.</p>
  <div class="abs tile" style="left:111px;background:linear-gradient(160deg,#1a3a6a,#3a7ab8 50%,#1a1a2a)" role="img" aria-label="Wedding venue lit in blue with a chandelier"></div>
  <div class="abs tile" style="left:359px;background:linear-gradient(135deg,#2a2a3a,#6a4a9a 55%,#1a1a22)" role="img" aria-label="DJ mixing controller"></div>
  <div class="abs tile" style="left:607px;background:linear-gradient(135deg,#f2ece6,#e9c3c8 50%,#cfd8c0)" role="img" aria-label="Pink and white wedding bouquet"></div>
  <div class="abs tile" style="left:855px;background:linear-gradient(135deg,#b88a5a,#d9b58a 50%,#7a5a3a)" role="img" aria-label="Business cards beside autumn pumpkins"></div>

  <!-- makes the night -->
  <div class="abs frame" style="left:130px;top:2027px;width:444px;height:361px"></div>
  <div class="abs photo" style="left:116px;top:2012px;width:441px;height:356px;border:2px solid #555;background:linear-gradient(150deg,#1a1a2a,#6a5a4a 45%,#c8b8a0 60%,#2a2a3a)" role="img" aria-label="Bride dancing with guests on the dancefloor"></div>
  <h2 class="abs h2" style="left:599px;top:2004px;font-size:36px">The DJ makes the night</h2>
  <p class="abs body" style="left:599px;top:2060px;width:490px">We believe that music is the 'make or break' of a party which is why we feel so passionately that this should be done right. With your top requests and favourite genres, Marrow and Tide use our vast knowledge of music to provide bespoke packages and playlists for your wedding or party to please the whole crowd.</p>
  <h2 class="abs h2" style="left:599px;top:2193px;font-size:36px">We get to know you</h2>
  <p class="abs body" style="left:599px;top:2248px;width:490px">We work closely with our clients on the run up to your big day to ensure your vision is achieved and executed to perfection. Our online music planner allows you to add your favourite tracks as they spring to mind and organise with ease. From the day you book, we will be on hand to answer any questions and to discuss your wedding music to ensure we create the perfect package for you.</p>

  <!-- working together -->
  <h3 class="abs h2" style="left:113px;top:2497px;font-size:23px">Working Together</h3>
  <p class="abs body" style="left:113px;top:2541px;width:490px">With experience of working with many popular wedding and party venues across London and Surrey, we work in partnership with venues, wedding planners, bands, musicians and other companies to ensure your big day is exactly as you want it.</p>
  <h3 class="abs h2" style="left:113px;top:2650px;font-size:23px">Looking for a DJ that’s a bit different?</h3>
  <p class="abs body" style="left:113px;top:2694px;width:490px">Marrow and Tide packages are tailored to suit you. We pay attention to the finer detail and add a touch of rustic class with our unique oak DJ booth which stands out from the usual star lit cloth.</p>
  <h3 class="abs h2" style="left:113px;top:2778px;font-size:23px">Our guarantee:</h3>
  <p class="abs body" style="left:113px;top:2822px;width:490px">Marrow and Tide Surrey DJ hire service know how to keep the dancefloor full. We promise to give you and your guests a night of unforgettable memories on the dancefloor, keeping the dancing going until the very last note of the night.</p>
  <div class="abs frame" style="left:629px;top:2509px;width:443px;height:391px"></div>
  <div class="abs photo" style="left:644px;top:2493px;width:443px;height:388px;border:2px solid #777;background:linear-gradient(135deg,#8a6a4a,#c8b090 45%,#9aa6c0 70%,#5a4a3a)" role="img" aria-label="DJ wearing headphones in a timber-framed venue"></div>

  <!-- reviews -->
  <h2 class="abs h2" style="left:0;top:2995px;width:1200px;text-align:center;font-size:34px">REVIEWS</h2>
  <div class="abs photo" style="left:111px;top:3065px;width:486px;height:335px;background:linear-gradient(160deg,#2a2a4a,#4a4a70 50%,#1a1a2a)" role="img" aria-label="Barn reception decorated with fairy lights and dressed tables"></div>
  <div class="abs" style="left:641px;top:3058px;width:91px;height:92px;border-radius:50%;background:linear-gradient(135deg,#c8a890,#8a6a5a)" role="img" aria-label="Reviewer portrait"></div>
  <div class="abs serif" style="left:747px;top:3068px;font-size:22px;color:#222">John doe</div>
  <div class="abs" style="left:747px;top:3108px;font-size:16px;font-weight:600;color:#555">Company name</div>
  <svg class="abs" style="left:1030px;top:3102px" width="16" height="20" viewBox="0 0 16 20"><path d="M11 3L4 10l7 7" fill="none" stroke="#333" stroke-width="2"/></svg>
  <svg class="abs" style="left:1076px;top:3102px" width="16" height="20" viewBox="0 0 16 20"><path d="M5 3l7 7-7 7" fill="none" stroke="#333" stroke-width="2"/></svg>
  <div class="abs" style="left:641px;top:3170px;width:447px;height:2px;background:#ddd"></div>
  <div class="abs stars" style="left:652px;top:3196px">★★★★★</div>
  <p class="abs" style="left:652px;top:3234px;width:430px;font-size:14px;line-height:21.6px;color:#555">Lorem ipsum dolor sit amet, consectetur adipiscing elit, sed do eiusmod tempor incididunt ut labore et dolore magna aliqua. Ut enim ad minim veniam, quis nostrud exercitation isi ut aliquip ex ea commodo consequat.</p>
  <div class="abs" style="left:641px;top:3350px;width:447px;height:2px;background:#ddd"></div>
  <div class="abs" style="left:652px;top:3381px;font-size:16px;font-weight:600;color:#555;display:flex;align-items:center;gap:5px">
    <svg width="15" height="15" viewBox="0 0 24 24"><path fill="#555" d="M2 10h4v12H2zM8 22V10l6-8c1.5 0 2.5 1 2 3l-1 4h6c1.2 0 2 1 1.8 2.2l-1.6 8.6c-.2 1.3-1.2 2.2-2.5 2.2z"/></svg>Useful</div>
  <div class="abs" style="left:774px;top:3381px;font-size:16px;font-weight:600;color:#555;display:flex;align-items:center;gap:7px">
    <svg width="17" height="15" viewBox="0 0 24 20"><path fill="#555" d="M14 0l10 8-10 8v-5C7 11 3 13 0 19 1 11 5 6 14 5z"/></svg>Share</div>

  <!-- contact -->
  <div class="abs frame" style="left:92px;top:3506px;width:971px;height:561px;border-color:#aaa"></div>
  <section class="abs contact"></section>
  <h2 class="abs h2" style="left:136px;top:3606px;width:971px;text-align:center;font-size:35px;color:#fff">CONTACT US</h2>
  <div class="abs field" style="left:246px;top:3671px;width:346px;height:48px">Name</div>
  <div class="abs field" style="left:609px;top:3671px;width:344px;height:48px">Phone</div>
  <div class="abs field" style="left:246px;top:3736px;width:346px;height:48px">Email address</div>
  <div class="abs field" style="left:609px;top:3736px;width:344px;height:48px">Subject</div>
  <div class="abs field" style="left:246px;top:3800px;width:707px;height:137px">Message</div>
  <div class="abs submit">SUBMIT</div>

  <!-- footer -->
  <div class="abs" style="left:0;top:4158px;width:1200px;text-align:center;font-size:13px;color:#222">© Copyrights 2021 Company name | All Rights Reserved</div>
  <div class="abs socials dark" style="left:510px;top:4202px">
    <span class="social"></span><span class="social"></span><span class="social"></span><span class="social"></span><span class="social"></span>
  </div>
</div>
</body>
</html>
```